Change of trading name, rebrand

existing website to be updated with new theme and logo. existing website is
www.harlowbrentmere.com.au
Industry/Entity Type
Construction
Coding
Coded - Design and coding required
Number of Pages Required
5+ page
Requirements
Must have
- be mobile phone friendly

```html
<!DOCTYPE html>
<html lang="en">
<head>
<meta charset="utf-8">
<meta name="viewport" content="width=device-width, initial-scale=1">
<title>HBE Heavy Equipment Hire</title>
<link href="https://fonts.googleapis.com/css2?family=Orbitron:wght@800;900&family=Poppins:wght@400;500;600;700&display=swap" rel="stylesheet">
<style>
:root{
  --navy:#25276f;
  --navy-deep:#1c1e5c;
  --ink:#111111;
  --text:#777777;
  --lav:#ebebf7;
  --white:#ffffff;
  --line:#d9d9e6;
}
*{box-sizing:border-box;margin:0;padding:0}
html,body{width:1200px;height:3553px;overflow:hidden}
body{position:relative;font-family:"Poppins",sans-serif;background:var(--white);color:var(--ink)}
.abs{position:absolute}
.display{font-family:"Orbitron",sans-serif;font-weight:900;letter-spacing:3px;color:var(--navy)}
.btn{position:absolute;display:flex;align-items:center;justify-content:center;background:var(--navy);color:var(--white);font-weight:600;font-size:14px;border-radius:26px;text-transform:uppercase}

/* header */
.topline{left:0;top:0;width:1200px;height:4px;background:var(--navy)}
.logo-tab{left:143px;top:4px;width:258px;height:135px;background:var(--white);clip-path:polygon(0 0,100% 0,100% 78%,94% 100%,6% 100%,0 78%);z-index:3;display:flex;align-items:center;justify-content:center;gap:10px}
.logo-mark{width:18px;height:18px;background:var(--navy)}
.logo-name{font-weight:700;font-size:22px;color:var(--navy);line-height:1.05}
.contact-bar{top:20px;left:695px;display:flex;align-items:center;gap:20px}
.contact-item{display:flex;align-items:center;gap:10px}
.ico-dot{width:28px;height:28px;border-radius:50%;background:var(--navy);display:flex;align-items:center;justify-content:center}
.phone-num{font-size:23px;font-weight:600}
.address{font-size:12px;line-height:16px}
.nav{top:77px;left:402px;display:flex;gap:24px;font-size:12px;font-weight:600;text-transform:uppercase}
.nav .active{color:var(--navy);border-left:2px solid var(--navy);padding-left:4px}

/* hero */
.hero{left:0;top:108px;width:1200px;height:537px;background:linear-gradient(180deg,#2c3a4c 0%,#4b5a68 45%,#6a5c50 70%,#5a5044 100%);clip-path:polygon(0 0,100% 0,100% 72%,0 100%)}
.hero-wedge{left:680px;top:532px;width:520px;height:74px;background:var(--navy);clip-path:polygon(100% 0,100% 100%,0 100%)}
.hero-title{left:521px;top:218px;font-size:44px;line-height:50px;color:var(--white);letter-spacing:4px}
.hero-sub{left:521px;top:333px;font-size:18px;font-weight:600;color:var(--white)}
.hero-btn{left:522px;top:386px;width:160px;height:51px}
.slider-dots{left:1123px;top:288px;display:flex;flex-direction:column;gap:8px}
.slider-dots span{width:8px;height:8px;border-radius:50%;background:var(--white)}
.slider-dots .on{width:12px;height:12px;border:2px solid var(--white);background:none;margin-left:-2px}

/* about */
.about-art{left:14px;top:965px;width:520px;height:166px;background:linear-gradient(90deg,#1a1a1a,#3a3a3a 60%,#1a1a1a)}
.about-photo{left:143px;top:648px;width:340px;height:340px;border-radius:50%;background:linear-gradient(180deg,#6f9fd0 0%,#b8cde0 40%,#3d4048 70%,#8a6d45 100%)}
.about-ring{left:165px;top:670px;width:296px;height:296px;border-radius:50%;border:3px solid var(--navy)}
.dots{background-image:radial-gradient(#cfcfdc 1.6px,transparent 1.8px);background-size:11px 11px}
.about-title{left:556px;top:658px;font-size:44px}
.about-text{left:556px;top:728px;width:498px;font-size:14px;line-height:24px;color:var(--text);text-align:justify}
.about-btn{left:556px;top:1014px;width:161px;height:51px}
.rule{left:0;width:1200px;height:5px;background:var(--ink)}

/* plant hire */
.plant{left:0;top:1145px;width:1200px;height:648px;background:var(--lav)}
.plant-title{left:0;top:1225px;width:1200px;text-align:center;font-size:44px}
.tabs{left:148px;top:1298px;display:flex;align-items:center;font-size:13.5px;font-weight:600;text-transform:uppercase}
.tabs .tab-on{background:var(--navy);color:var(--white);padding:8px 15px;border-radius:20px;margin-right:12px}
.tabs .sep{margin:0 9px}
.card{left:143px;top:1372px;width:912px;height:338px;background:var(--white);box-shadow:0 4px 10px rgba(0,0,0,.1)}
.card-photo{left:143px;top:1372px;width:387px;height:338px;background:linear-gradient(180deg,#7fb0de 0%,#c9c9c2 35%,#c95a2a 55%,#b48c5c 100%)}
.card-title{left:592px;top:1400px;font-size:25px;font-weight:600}
.card-text{left:592px;top:1445px;width:408px;font-size:12.5px;line-height:23.5px;color:var(--text);text-align:justify}
.card-btn{left:592px;top:1626px;width:161px;height:51px}

/* stats */
.stat{top:1825px;width:200px;text-align:center;font-size:15px;line-height:25px;text-transform:uppercase}
.stat svg{display:block;margin:0 auto 14px}
.stat b{display:block;font-size:22px;font-weight:700}

/* contact */
.contact-photo{left:0;top:1990px;width:600px;height:617px;background:linear-gradient(160deg,#8fb0d8 0%,#c8c2a0 40%,#e2b92a 60%,#3b3b3b 100%)}
.contact-panel{left:496px;top:1979px;width:691px;height:628px;background:var(--navy);clip-path:polygon(0 0,100% 0,100% 100%,15% 100%)}
.contact-art{left:607px;top:2400px;width:593px;height:207px;background:linear-gradient(90deg,#121212,#2d2d2d 50%,#121212);clip-path:polygon(3% 40%,100% 30%,100% 100%,0 100%)}
.contact-title{left:632px;top:2058px;font-size:44px;color:var(--white)}
.contact-sub{left:632px;top:2123px;font-size:19px;font-weight:600;color:var(--white)}
.field{position:absolute;border:1px solid rgba(255,255,255,.5);color:var(--white);font-size:13.5px;padding:15px 24px}
.submit{left:632px;top:2419px;width:161px;height:51px;background:var(--white);color:var(--navy)}

/* partners */
.partners-title{left:0;top:2705px;width:1200px;text-align:center;font-size:44px}
.partner-grid{left:145px;top:2802px;width:910px;height:225px;display:grid;grid-template-columns:repeat(4,1fr);grid-template-rows:1fr 1fr;border:1px solid var(--line);border-radius:6px;background:var(--white)}
.partner-grid div{border:1px solid var(--line);display:flex;align-items:center;justify-content:center}
.partner-grid span{width:120px;height:34px;border-radius:6px;background:#d7d8e6}
.pdots{left:570px;top:3071px;display:flex;gap:16px}
.pdots span{width:7px;height:7px;border-radius:50%;background:#9a9a9a}
.pdots .on{background:var(--navy)}

/* footer */
.footer{left:0;top:3110px;width:1200px;height:443px;background:#000;clip-path:polygon(0 0,100% 0,100% 100%,0 100%)}
.footer-wedge{left:0;top:3110px;width:560px;height:85px;background:var(--navy);clip-path:polygon(0 0,100% 0,0 100%)}
.footer-white{left:0;top:3080px;width:1200px;height:30px;background:var(--white);clip-path:polygon(0 0,100% 0,100% 100%,0 100%)}
.footer-logo{left:145px;top:3240px;display:flex;align-items:center;gap:12px;color:var(--white);font-weight:700;font-size:28px;line-height:1.1}
.footer-logo i{width:22px;height:22px;background:var(--white)}
.f-head{top:3256px;color:var(--white);font-size:15px;font-weight:600;text-transform:uppercase}
.f-row{left:525px;display:flex;align-items:center;gap:18px;color:var(--white);font-size:12px;line-height:17px}
.f-ring{width:34px;height:34px;border-radius:50%;border:2px solid var(--white);display:flex;align-items:center;justify-content:center}
.f-links{top:3297px;color:var(--white);font-size:12px;line-height:25.5px;list-style:none}
.f-rule{left:145px;top:3447px;width:910px;height:1px;background:#333}
.copy{left:145px;top:3497px;color:var(--white);font-size:11.5px}
.social{top:3488px;display:flex;gap:12px;left:926px}
.social span{width:35px;height:35px;border-radius:50%;background:var(--white)}
</style>
</head>
<body>

<header>
  <div class="abs topline"></div>
  <div class="abs logo-tab"><span class="logo-mark"></span><span class="logo-name">HBE<br>PLANT HIRE</span></div>
  <div class="abs contact-bar">
    <div class="contact-item">
      <span class="ico-dot"><svg width="14" height="14" viewBox="0 0 24 24"><path fill="#fff" d="M6.6 10.8a15 15 0 0 0 6.6 6.6l2.2-2.2c.3-.3.7-.4 1-.2 1.1.4 2.3.6 3.6.6.6 0 1 .4 1 1V20c0 .6-.4 1-1 1A17 17 0 0 1 3 4c0-.6.4-1 1-1h3.5c.6 0 1 .4 1 1 0 1.3.2 2.5.6 3.6.1.3 0 .7-.2 1z"/></svg></span>
      <span class="phone-num">1300 555 014</span>
    </div>
    <div class="contact-item">
      <span class="ico-dot"><svg width="14" height="14" viewBox="0 0 24 24"><path fill="#fff" d="M12 2a7 7 0 0 0-7 7c0 5 7 13 7 13s7-8 7-13a7 7 0 0 0-7-7zm0 9.5a2.5 2.5 0 1 1 0-5 2.5 2.5 0 0 1 0 5z"/></svg></span>
      <span class="address">18 Wattle Ridge Rd,<br>Coomera Vale QLD 4299</span>
    </div>
  </div>
  <nav class="abs nav">
    <span class="active">Home</span><span>About us</span><span>Plant hire</span><span>Major project snapshot</span><span>Policies</span><span>Jobs</span><span>Contact us</span>
  </nav>
</header>

<section>
  <div class="abs hero" role="img" aria-label="Excavator on a worksite under a stormy sky"></div>
  <div class="abs hero-wedge"></div>
  <h1 class="abs display hero-title">HBE HEAVY<br>EQUIPMENT HIRE</h1>
  <p class="abs hero-sub">Committed to superior quality plant hire services.</p>
  <span class="btn hero-btn">Get started</span>
  <div class="abs slider-dots"><span></span><span class="on"></span><span></span></div>
  <svg class="abs" style="left:590px;top:568px" width="18" height="48" viewBox="0 0 18 48"><rect x="2" y="1" width="14" height="22" rx="7" fill="none" stroke="#111" stroke-width="2"/><line x1="9" y1="6" x2="9" y2="11" stroke="#111" stroke-width="2"/><path d="M4 30l5 5 5-5M4 38l5 5 5-5" fill="none" stroke="#111" stroke-width="2"/></svg>
</section>

<section>
  <div class="abs dots" style="left:92px;top:780px;width:60px;height:120px"></div>
  <div class="abs dots" style="left:1083px;top:1088px;width:117px;height:56px"></div>
  <div class="abs about-photo" role="img" aria-label="Stacked pipes and loaders in a plant yard"></div>
  <div class="abs about-ring"></div>
  <div class="abs about-art" role="img" aria-label="Silhouette of a roller and an excavator on rubble"></div>
  <h2 class="abs display about-title">ABOUT US</h2>
  <p class="abs about-text">Harlow Brentmere Heavy Equipment Hire specialise in the hire of heavy earthmoving, mining and construction machines with specialised attachments and tooling. Our array of machines and attachments is second to none, and we have one of the largest hire fleets available in South East Queensland. If its plant hire you require, then Harlow Brentmere Resources, or HBE as the local's call us – should be the first call you make. Wet or dry hire, we provide excellent operators and quality machines across all makes and models to guarantee you maximum up-time.We employ a group of highly skilled and capable managers who have worked throughout construction sites in Queensland, NSW and other parts of Australia to deliver a vast array of plant and equipment to mining.</p>
  <span class="btn about-btn">Read more</span>
  <div class="abs rule" style="top:1132px"></div>
</section>

<section>
  <div class="abs plant"></div>
  <h2 class="abs display plant-title">PLANT HIRE</h2>
  <div class="abs tabs">
    <span class="tab-on">Excavators</span><span>Dozers</span><span class="sep">|</span><span>Dump trucks</span><span class="sep">|</span><span>Graders</span><span class="sep">|</span><span>Loaders</span><span class="sep">|</span><span>Bobcats</span><span class="sep">|</span><span>Water carts</span><span class="sep">|</span><span>Backhoes</span><span class="sep">|</span><span>Compactors</span>
  </div>
  <div class="abs card"></div>
  <div class="abs card-photo" role="img" aria-label="Orange excavator digging a trench beside a fence"></div>
  <h3 class="abs card-title">EXCAVATORS AND DIGGERS</h3>
  <p class="abs card-text">HBE Heavy Equipment has one of the largest fleet of excavators for hire in South East Queensland, north to Sunshine Coast, south into Northern New South Wales and inland to the Surat Basin, Toowoomba and Dalby.We are proud of our broad range of excavators fitted with state-of-the-art GPS, spanning reliable and trusted brands such as Ironvale excavators for hire, Kestrel excavators for hire.</p>
  <span class="btn card-btn">Read more</span>
</section>

<section>
  <div class="abs stat" style="left:128px"><svg width="26" height="28" viewBox="0 0 26 28"><rect x="1" y="5" width="24" height="22" rx="2" fill="#25276f"/><rect x="6" y="1" width="3" height="7" fill="#25276f"/><rect x="17" y="1" width="3" height="7" fill="#25276f"/><rect x="1" y="10" width="24" height="1.5" fill="#fff"/></svg><b>20+</b>Years of experience</div>
  <div class="abs stat" style="left:348px"><svg width="34" height="28" viewBox="0 0 34 28"><rect x="1" y="4" width="20" height="16" fill="#25276f"/><path d="M21 9h7l5 6v5H21z" fill="#25276f"/><circle cx="8" cy="22" r="4" fill="#25276f" stroke="#fff" stroke-width="2"/><circle cx="26" cy="22" r="4" fill="#25276f" stroke="#fff" stroke-width="2"/></svg><b>100+</b>Machines in fleet</div>
  <div class="abs stat" style="left:558px"><svg width="32" height="28" viewBox="0 0 32 28"><path d="M1 5l9-3 12 4 9-3v20l-9 3-12-4-9 3z" fill="#25276f"/><path d="M10 2v20M22 6v20" stroke="#fff" stroke-width="1.5"/></svg>One of QLD'S<br>largest suppliers</div>
  <div class="abs stat" style="left:732px"><svg width="28" height="28" viewBox="0 0 24 24"><path fill="#25276f" d="M19.4 13a7.5 7.5 0 0 0 0-2l2.1-1.6-2-3.5-2.5 1a7 7 0 0 0-1.7-1L15 3h-4l-.4 2.7a7 7 0 0 0-1.7 1l-2.5-1-2 3.5L6.6 11a7.5 7.5 0 0 0 0 2l-2.1 1.6 2 3.5 2.5-1a7 7 0 0 0 1.7 1L11 21h4l.4-2.7a7 7 0 0 0 1.7-1l2.5 1 2-3.5zM13 15.5a3.5 3.5 0 1 1 0-7 3.5 3.5 0 0 1 0 7z"/></svg>Onsite<br>servicing</div>
  <div class="abs stat" style="left:886px"><svg width="22" height="28" viewBox="0 0 22 28"><path d="M1 1h13l7 7v19H1z" fill="#25276f"/><path d="M14 1v7h7" fill="#fff"/></svg>Custom machine<br>attachments</div>
  <div class="abs dots" style="left:1058px;top:1926px;width:118px;height:33px"></div>
</section>

<section>
  <div class="abs contact-photo" role="img" aria-label="Yellow backhoe loader parked in a yard"></div>
  <div class="abs contact-panel"></div>
  <div class="abs contact-art" role="img" aria-label="Silhouette of a roller and excavators on rubble"></div>
  <h2 class="abs display contact-title">CONTACT US</h2>
  <p class="abs contact-sub">Contact us today for a FREE QUOTE</p>
  <div class="field" style="left:632px;top:2181px;width:207px;height:50px">Enter Name</div>
  <div class="field" style="left:848px;top:2181px;width:207px;height:50px">Enter Email</div>
  <div class="field" style="left:632px;top:2245px;width:423px;height:51px">Phone</div>
  <div class="field" style="left:632px;top:2310px;width:423px;height:90px">Enquiry</div>
  <span class="btn submit">Submit</span>
  <div class="abs rule" style="top:2605px;left:595px;width:605px"></div>
</section>

<section>
  <h2 class="abs display partners-title">OUR PARTNERS</h2>
  <div class="abs dots" style="left:100px;top:2755px;width:118px;height:110px"></div>
  <div class="abs dots" style="left:985px;top:2950px;width:118px;height:118px"></div>
  <div class="abs partner-grid">
    <div><span></span></div><div><span></span></div><div><span></span></div><div><span></span></div>
    <div><span></span></div><div><span></span></div><div><span></span></div><div><span></span></div>
  </div>
  <div class="abs pdots"><span></span><span class="on"></span><span></span></div>
</section>

<footer>
  <div class="abs footer"></div>
  <div class="abs footer-wedge"></div>
  <div class="abs footer-logo"><i></i><span>HBE<br>PLANT HIRE</span></div>
  <h4 class="abs f-head" style="left:525px">Contact information</h4>
  <div class="abs f-row" style="top:3294px"><span class="f-ring"><svg width="12" height="14" viewBox="0 0 24 24"><path fill="none" stroke="#fff" stroke-width="2.5" d="M12 2a7 7 0 0 0-7 7c0 5 7 13 7 13s7-8 7-13a7 7 0 0 0-7-7z"/></svg></span><span>18 Wattle Ridge Rd,<br>Coomera Vale QLD 4299</span></div>
  <div class="abs f-row" style="top:3346px"><span class="f-ring"><svg width="13" height="13" viewBox="0 0 24 24"><path fill="#fff" d="M6.6 10.8a15 15 0 0 0 6.6 6.6l2.2-2.2c.3-.3.7-.4 1-.2 1.1.4 2.3.6 3.6.6.6 0 1 .4 1 1V20c0 .6-.4 1-1 1A17 17 0 0 1 3 4c0-.6.4-1 1-1h3.5c.6 0 1 .4 1 1 0 1.3.2 2.5.6 3.6.1.3 0 .7-.2 1z"/></svg></span><span>Phone : 1300 555 014</span></div>
  <h4 class="abs f-head" style="left:812px">Links</h4>
  <ul class="abs f-links" style="left:812px"><li>Home</li><li>About us</li><li>Plant hire</li><li>Major project snapshot</li></ul>
  <ul class="abs f-links" style="left:989px;top:3300px"><li>Policies</li><li>Jobs</li><li>Contact us</li></ul>
  <div class="abs f-rule"></div>
  <p class="abs copy">© 2024 Harlow Brentmere Heavy Equipment Hire. All rights reserved.Privacy &nbsp;| &nbsp;Terms of Use</p>
  <div class="abs social"><span></span><span></span><span></span></div>
</footer>

</body>
</html>
```